Design and Renovation Company Luxury Business Card

I want to create a luxury business card for a Design and Renovation Firm . We will use our current logo. The company name is 528BUILDA. We do not want anything standard. We need a very unique concept.
Please see uploaded inspiration. I really like the textured paper option. I would like the card to be thick with debossing, and/or embossing options. The logo has orange in it but I would like to see the card with and without the orange. I think the orange may make the company feel less high-end. The goal is to elevate the logo not match its vibe per se of the logo. We want something very unique, not standard at all!
I would like a space for :
Logo,
Name,
Position,
Email,
Office number,
Website Address,
Business Address,
Thank you!
Have fun!
Target Market(s)
Home owners Age 35 +
Industry/Entity Type
Design and Renovation
Contact Information for Business Card
Logo, Name, Position, Email, Office number, Website Address, Business Address,.
Colors
Designer to choose colors to be used in the design.
Requirements
Must have
- A luxury designer feel. Must be black or dark grey but open to other luxury ideas.
Nice to have
- Gold, silver, black embossing or debossing. Textured paper design.
Should not have
- A cheap look and feel.

```html
<!DOCTYPE html>
<html lang="en">
<head>
<meta charset="utf-8">
<title>528BUILDA Business Card</title>
<link rel="stylesheet" href="https://fonts.googleapis.com/css2?family=Saira:wght@700&family=Rubik:wght@400&display=swap">
<style>
  :root {
    --backdrop: #2a2a2c;
    --card: #303032;
    --card-edge: #262628;
    --ink-muted: #8c8c8e;
    --ink-tagline: #6a6a6c;
    --text-light: #d4d4d6;
    --accent: #f7941d;
    --grid-light: #9a9a9c;
    --grid-dark: #030303;
  }
  * { margin: 0; padding: 0; box-sizing: border-box; }
  html, body {
    width: 1200px; height: 799px; overflow: hidden;
    background: var(--backdrop);
  }
  .stage {
    position: relative; width: 1200px; height: 799px;
    display: flex; align-items: center; justify-content: center; gap: 40px;
  }
  .card {
    position: relative; width: 540px; height: 309px;
    background: var(--card);
    border: 1px solid var(--card-edge);
    border-radius: 3px;
    box-shadow: 0 10px 30px rgba(0,0,0,0.35);
    overflow: hidden;
  }
  .card-front__pattern {
    position: absolute; inset: 0;
    background: linear-gradient(45deg, var(--grid-light) 0%, #4a4a4c 40%, #151516 70%, var(--grid-dark) 100%);
  }
  .brand {
    position: absolute; top: 44px; left: 0; right: 0;
    text-align: center;
  }
  .brand__name {
    font-family: "Rubik", sans-serif; font-weight: 400;
    font-size: 40px; letter-spacing: 4px; line-height: 1;
    color: var(--ink-muted);
  }
  .brand__tagline {
    margin-top: 14px;
    font-family: "Rubik", sans-serif; font-weight: 400;
    font-size: 12px; letter-spacing: 5px;
    color: var(--ink-tagline);
  }
  .person {
    position: absolute; top: 170px; left: 36px; width: 210px; text-align: right;
  }
  .person__name {
    font-family: "Saira", sans-serif; font-weight: 700;
    font-size: 22px; letter-spacing: 1px; line-height: 1.2; color: var(--accent);
  }
  .person__role {
    font-family: "Rubik", sans-serif; font-size: 13px;
    color: var(--text-light); margin-top: 4px;
  }
  .divider {
    position: absolute; top: 160px; left: 266px;
    width: 1px; height: 96px; background: var(--accent);
  }
  .contact {
    position: absolute; top: 162px; left: 286px;
    list-style: none;
    font-family: "Rubik", sans-serif; font-size: 12px; line-height: 1.35;
    color: var(--text-light);
  }
  .contact li { display: flex; align-items: flex-start; gap: 9px; margin-bottom: 4px; }
  .contact svg { width: 11px; height: 11px; flex: none; margin-top: 2px; fill: var(--accent); }
</style>
</head>
<body>
<main class="stage">
  <section class="card card-front">
    <div class="card-front__pattern" role="img" aria-label="Grid of small square tiles fading from silver to black across the card"></div>
  </section>

  <section class="card card-back">
    <div class="brand">
      <p class="brand__name">528BUILDA</p>
      <p class="brand__tagline">Design and Renovation Firm</p>
    </div>

    <div class="person">
      <h1 class="person__name">DANIEL HARLOW</h1>
      <p class="person__role">Founder &amp; CEO</p>
    </div>

    <span class="divider"></span>

    <ul class="contact">
      <li>
        <svg viewBox="0 0 12 12" aria-hidden="true"><path d="M6 0a4 4 0 0 0-4 4c0 3 4 8 4 8s4-5 4-8a4 4 0 0 0-4-4zm0 5.5A1.5 1.5 0 1 1 6 2.5a1.5 1.5 0 0 1 0 3z"/></svg>
        <span>423 Street Address Here, City<br>State, Country, ZIP Code</span>
      </li>
      <li>
        <svg viewBox="0 0 12 12" aria-hidden="true"><path d="M2.5 0.5l2 2.5-1 1.3a7 7 0 0 0 4.2 4.2l1.3-1 2.5 2-1.2 1.8C5 11 1 7 .7 1.7z"/></svg>
        <span>+1 1234 567 892</span>
      </li>
      <li>
        <svg viewBox="0 0 12 12" aria-hidden="true"><path d="M0 2h12v8H0zM0.8 2.6L6 6.6l5.2-4v.9L6 7.6.8 3.5z"/></svg>
        <span>info@yourwebsitehere.com</span>
      </li>
      <li>
        <svg viewBox="0 0 12 12" aria-hidden="true"><path d="M6 0a6 6 0 1 0 0 12A6 6 0 0 0 6 0zm0 1.2c.8 0 1.6 1.8 1.7 4.2H4.3C4.4 3 5.2 1.2 6 1.2zM4.3 6.6h3.4C7.6 9 6.8 10.8 6 10.8S4.4 9 4.3 6.6zM1.2 5.4a4.8 4.8 0 0 1 2.4-3.7c-.3.9-.5 2.2-.5 3.7zm0 1.2h1.9c0 1.5.2 2.8.5 3.7a4.8 4.8 0 0 1-2.4-3.7zm9.6 0a4.8 4.8 0 0 1-2.4 3.7c.3-.9.5-2.2.5-3.7zm0-1.2H8.9c0-1.5-.2-2.8-.5-3.7a4.8 4.8 0 0 1 2.4 3.7z"/></svg>
        <span>yourwebsitehere.com</span>
      </li>
    </ul>
  </section>
</main>
</body>
</html>
```